Investment Memorandum Document

IM for Harbourline Lending Fund - is the document that needs work

Make sure it is all done in MS WORD so that i or lawyers can edit some words if required

the IM is NOT final but its 95% of the way there. Maybe a few more pages and wording changes - but that is something i can do i guess or you can easier adjust

Just to typeset and pretty it all up - a few sample finished products have been uploaded for reference.

KTR IM is the one i like - but feel free to show off your skills

put 1.2 to 1.8 all in contrasting row tables

Target Market(s)

Individual and Institutional investors with money

Industry/Entity Type

Investment Banking

Colors

Designer to choose colors to be used in the design.

Requirements
Must have
• clear professional layout and easy on the eye
• https://www.filevaultexample.net/sh/84k3p77zrm2wqtn/BBDfpqWem3PvtsLxQZMUD41Lb?dl=0
• use the link above for high res images
Nice to have
• pictures and graphics
Should not have
• cartoons

```html
<!DOCTYPE html>
<html lang="en">
<head>
<meta charset="utf-8">
<title>Harbourline Diversified Commercial Income Fund – Information Memorandum, Page 2</title>
<link rel="stylesheet" href="https://fonts.googleapis.com/css2?family=Roboto:ital,wght@0,300;0,400;0,500;1,300&display=swap">
<style>
  :root {
    --backdrop: #808080;
    --paper: #fafafa;
    --ink: #4a4a4a;
    --gold: #c2a36b;
    --box-grey: #6e6e6e;
    --fund-green: #6cb24a;
    --unit-blue: #dde7f6;
    --arrow: #3c3c3c;
    --footer-dark: #3b4043;
  }
  * { box-sizing: border-box; margin: 0; padding: 0; }
  html, body { width: 1096px; height: 1200px; overflow: hidden; background: var(--backdrop); }
  body { position: relative; font-family: "Roboto", Arial, sans-serif; color: var(--ink); }

  .page {
    position: absolute; left: 219px; top: 135px;
    width: 809px; height: 1144px;
    background: var(--paper);
    transform: scale(0.8125); transform-origin: top left;
  }

  .section-title { position: absolute; left: 58px; top: 95px; font-size: 22px; font-weight: 400; color: var(--gold); }
  .sub-title { position: absolute; left: 58px; top: 141px; font-size: 12.5px; font-weight: 300; color: var(--gold); }
  .sub-title .num { display: inline-block; width: 40px; padding-left: 10px; }

  .copy { position: absolute; left: 58px; width: 692px; font-size: 12.6px; font-weight: 300; line-height: 16.4px; text-align: justify; }
  .copy p { text-indent: 10px; margin-bottom: 4.5px; }
  .copy ul { list-style: none; margin-bottom: 4.5px; }
  .copy li { position: relative; padding-left: 24px; margin-bottom: 4.5px; }
  .copy li::before { content: "»"; position: absolute; left: 11px; top: 0; }
  .copy h3 { font-size: 12.6px; font-weight: 400; color: var(--gold); margin-bottom: 4.5px; }
  .intro { top: 162px; }
  .body-text { top: 634px; }

  .diagram { position: absolute; left: 0; top: 0; }
  .node { position: absolute; display: flex; flex-direction: column; align-items: center; justify-content: center; text-align: center; color: #fff; font-size: 11px; line-height: 14px; }
  .node strong { font-size: 12.5px; font-weight: 500; line-height: 15px; }
  .node--grey { background: var(--box-grey); border: 1px dashed #9a9a9a; }
  .node--fund { background: var(--fund-green); font-size: 13px; line-height: 16px; }
  .node--unit { background: var(--unit-blue); color: #2d2d2d; font-size: 13px; }
  .investors { left: 332px; top: 249px; width: 123px; height: 51px; }
  .manager { left: 61px; top: 370px; width: 169px; height: 62px; }
  .fund { left: 311px; top: 371px; width: 166px; height: 56px; }
  .trustee { left: 558px; top: 350px; width: 190px; height: 99px; }
  .trustee strong + span { margin-bottom: 5px; }
  .unit-cash { left: 91px; top: 549px; width: 156px; height: 59px; }
  .unit-c1 { left: 315px; top: 549px; width: 157px; height: 59px; }
  .unit-c2 { left: 538px; top: 549px; width: 158px; height: 59px; }

  .flow-label { position: absolute; font-size: 10.5px; font-style: italic; font-weight: 300; line-height: 13.5px; color: #333; text-align: center; }

  .footer-title { position: absolute; left: 58px; top: 1083px; font-size: 13px; font-weight: 300; }
  .footer-tab { position: absolute; left: 647px; top: 1074px; width: 162px; height: 34px; background: var(--footer-dark); color: #fff; display: flex; align-items: center; padding-left: 14px; gap: 8px; font-size: 13.5px; }
  .footer-tab .brand { font-size: 10px; font-weight: 400; color: #fff; display: flex; align-items: center; gap: 4px; }
  .footer-tab .brand i { display: inline-block; width: 7px; height: 7px; background: #fff; }
</style>
</head>
<body>
<main class="page">
  <h1 class="section-title">1) The Fund</h1>
  <h2 class="sub-title"><span class="num">1.1</span>Fund Outline</h2>

  <div class="copy intro">
    <p>The Fund is an unregistered managed investment scheme which pools Investors' monies and invests in loans predominantly used for property investment and development projects in Australia. The Fund was established by a Trust Deed dated XXX which regulates the relationship between the Trustee and Investors.&nbsp; The Trustee has appointed as the investment manager of the Fund pursuant to the Investment Management Agreement.</p>
  </div>

  <section class="diagram" aria-label="Fund structure">
    <svg width="809" height="620" style="position:absolute;left:0;top:0">
      <defs>
        <marker id="head" markerWidth="8" markerHeight="8" refX="6" refY="4" orient="auto">
          <path d="M0,1 L7,4 L0,7 z" fill="var(--arrow)"/>
        </marker>
      </defs>
      <g stroke="var(--arrow)" stroke-width="1.6" fill="none" marker-end="url(#head)">
        <line x1="383" y1="308" x2="383" y2="360"/>
        <line x1="405" y1="362" x2="405" y2="310"/>
        <line x1="383" y1="438" x2="383" y2="492"/>
        <line x1="405" y1="494" x2="405" y2="440"/>
        <line x1="241" y1="399" x2="294" y2="399"/>
        <line x1="542" y1="401" x2="490" y2="401"/>
        <line x1="170" y1="514" x2="170" y2="539"/>
        <line x1="393" y1="514" x2="393" y2="539"/>
        <line x1="616" y1="514" x2="616" y2="539"/>
      </g>
      <line x1="170" y1="514" x2="616" y2="514" stroke="var(--arrow)" stroke-width="1.6"/>
    </svg>

    <div class="node node--grey investors"><strong>Qualifying<br>Investors</strong></div>
    <div class="node node--grey manager"><strong>Investment Manager</strong><span>Harbourline Asset<br>Management Pty Ltd</span></div>
    <div class="node node--fund fund">Harbourline Diversified<br>Commercial Income Fund</div>
    <div class="node node--grey trustee">
      <strong>Wholesale Trustee</strong>
      <span>Kestrel Trust and<br>Lending Corporation Pty Ltd</span>
      <strong>Administrator</strong>
      <span>Kestrel Funds Administration Pty Ltd</span>
    </div>
    <div class="node node--unit unit-cash">Cash Unit</div>
    <div class="node node--unit unit-c1">Class 1 Loan Units</div>
    <div class="node node--unit unit-c2">Class 2 Loan Units</div>

    <span class="flow-label" style="left:322px;top:322px;width:58px">Invest in<br>Fund</span>
    <span class="flow-label" style="left:412px;top:315px;width:76px">Receive<br>interest<br>distributions</span>
    <span class="flow-label" style="left:242px;top:368px;width:60px">Provide<br>Services</span>
    <span class="flow-label" style="left:484px;top:371px;width:70px">Administers<br>Fund</span>
    <span class="flow-label" style="left:328px;top:457px;width:46px">Invest</span>
    <span class="flow-label" style="left:414px;top:441px;width:74px">Receives<br>interest and<br>principal<br>payments</span>
  </section>

  <div class="copy body-text">
    <p>The Fund will invest predominantly in loans used in connection with development projects managed or developed by Northgate Property Group.</p>
    <p>All investments are made in accordance with the Fund's Lending Guidelines. Please see section 2.1 for more information.</p>
    <p>The Fund is structured to allow Qualifying Investors to acquire interests in:</p>
    <ul>
      <li>A class of Cash Units in the Fund that are referable to a Basic Deposit Products which include cash management accounts and term deposits. In this way, Investors are able to effectively select the level of participation they have in each of the loans offered.</li>
      <li>A class of Loan Units in the Fund that are referable to a portfolio of loans which may comprise loans that may be unsecured or secured by a mixture of either first mortgages, second mortgages (which may or may not be registered) or other Security Interests. These portfolios are managed by the Investment Manager.</li>
    </ul>
    <h3>Key Benefits of Investing in the Fund</h3>
    <ul>
      <li>The Fund has an independent trustee that will provide an enhanced level of oversight ensuring that loans are made in accordance with this Information Memorandum and the Trust Deed. See Section 5 for information about the Trustee.</li>
      <li>The underlying Projects are undertaken and managed by a property investment group with extensive experience and track record across a variety of project types.</li>
      <li>Transparency through regular investment reports prepared by the Trustee.</li>
      <li>Accounting, financial reporting and tax affairs of the Fund managed by the Trustee to ensure independence, transparency and governance.</li>
      <li>Audited by Carrow &amp; Lyle Auditors</li>
    </ul>
  </div>

  <footer>
    <p class="footer-title">Harbourline Diversified Commercial Income Fund – Information Memorandum</p>
    <div class="footer-tab"><span class="brand"><i></i>Harbourline</span><span>Page 2</span></div>
  </footer>
</main>
</body>
</html>
```